New Business Card Design

We would like to refresh our business cards and make them look better. We are an IT company specialising in Cloud Services, IT Managed Services, software and hardware. I have attached a PSD of our current design. Also attached our logo.
Updates

I have uploaded all new logos in EPS format.

Can you please edit all designs to include a job title for Marcus Hollis, eg. General Manager

Industry/Entity Type

Software

Colors
ffffff

Requirements
Must have
• Please use white background.
Should not have
• Black background

```html
<!DOCTYPE html>
<html lang="en">
<head>
<meta charset="utf-8">
<title>Meridian Technology – Business Card</title>
<link rel="stylesheet" href="https://fonts.googleapis.com/css2?family=Open+Sans:wght@400;600;700&display=swap">
<style>
  :root {
    --brand-red: #c23a2b;
    --ink: #2b2b2b;
    --ink-soft: #555555;
    --rule: #b9b9b9;
    --paper: #ffffff;
    --stage: #ecebe8;
  }
  * { box-sizing: border-box; margin: 0; padding: 0; }
  html, body {
    width: 1200px; height: 720px; overflow: hidden;
    background: var(--stage);
    font-family: "Open Sans", Arial, sans-serif;
  }
  .sheet {
    width: 1200px; height: 720px;
    display: flex; align-items: center; justify-content: center; gap: 40px;
  }
  .card {
    width: 540px; height: 309px;
    position: relative;
    box-shadow: 0 4px 14px rgba(0,0,0,0.15);
  }

  /* Front */
  .card--front { background: var(--paper); }
  .brand {
    position: absolute; left: 40px; top: 48px;
    display: flex; align-items: center; gap: 16px;
  }
  .brand__dot {
    width: 50px; height: 50px; border-radius: 50%;
    background: var(--brand-red);
  }
  .brand__name {
    font-weight: 600; color: var(--ink);
    font-size: 26px; line-height: 1.2;
  }
  .person {
    position: absolute; left: 40px; bottom: 40px;
  }
  .person__name { color: var(--brand-red); font-weight: 700; font-size: 18px; }
  .person__title { color: var(--ink); font-size: 13px; margin-top: 2px; }
  .person__mobile { display: flex; align-items: center; gap: 8px; margin-top: 8px; font-size: 13px; color: var(--ink-soft); }
  .contacts {
    position: absolute; left: 300px; top: 150px; bottom: 40px;
    border-left: 1px solid var(--rule);
    padding-left: 14px;
    list-style: none;
  }
  .contacts li {
    display: flex; align-items: center; gap: 8px;
    font-size: 13px; color: var(--ink-soft); line-height: 24px;
  }
  .icon { width: 14px; height: 14px; flex: none; }

  /* Back */
  .card--back {
    background: var(--brand-red); color: var(--paper);
    display: flex; flex-direction: column; align-items: center; text-align: center;
  }
  .back-brand { display: flex; align-items: center; gap: 14px; margin-top: 60px; }
  .back-brand__dot { width: 64px; height: 64px; border-radius: 50%; background: var(--paper); }
  .back-brand__name { font-weight: 600; font-size: 24px; }
  .tagline { margin-top: 40px; font-size: 16px; line-height: 1.45; }
  .back-web { margin-top: 12px; font-size: 13px; letter-spacing: 4px; }
</style>
</head>
<body>
<main class="sheet">
  <section class="card card--front" aria-label="Card front">
    <div class="brand">
      <div class="brand__dot"></div>
      <div class="brand__name">Meridian Technology</div>
    </div>

    <div class="person">
      <p class="person__name">Marcus Hollis</p>
      <p class="person__title">General Manager</p>
      <p class="person__mobile">
        <svg class="icon" viewBox="0 0 14 14" aria-hidden="true"><rect x="3.5" y="1" width="7" height="12" rx="1.5" fill="var(--brand-red)"/><rect x="5" y="3" width="4" height="6" fill="#fff"/></svg>
        0491 570 156
      </p>
    </div>

    <ul class="contacts">
      <li>
        <svg class="icon" viewBox="0 0 14 14" aria-hidden="true"><circle cx="7" cy="7" r="7" fill="var(--brand-red)"/><path d="M4.6 3.6l1.4 1.6-.8 1c.5 1 1.2 1.7 2.2 2.2l1-.8 1.6 1.4-.9 1.2C6.7 10 4 7.3 3.4 4.5z" fill="#fff"/></svg>
        07 3100 4580
      </li>
      <li>
        <svg class="icon" viewBox="0 0 14 14" aria-hidden="true"><circle cx="7" cy="7" r="7" fill="var(--brand-red)"/><rect x="3.5" y="4.5" width="7" height="5" fill="#fff"/><path d="M3.5 4.5L7 7.5l3.5-3" stroke="var(--brand-red)" stroke-width="0.8" fill="none"/></svg>
        mhollis@meridianit.com.au
      </li>
      <li>
        <svg class="icon" viewBox="0 0 14 14" aria-hidden="true"><circle cx="7" cy="7" r="7" fill="var(--brand-red)"/><circle cx="7" cy="7" r="3.6" fill="none" stroke="#fff" stroke-width="0.9"/><path d="M3.4 7h7.2M7 3.4v7.2" stroke="#fff" stroke-width="0.9"/></svg>
        www.meridianit.com.au
      </li>
    </ul>
  </section>

  <section class="card card--back" aria-label="Card back">
    <div class="back-brand">
      <div class="back-brand__dot"></div>
      <div class="back-brand__name">Meridian Technology</div>
    </div>
    <p class="tagline">We are an IT company specializing in Cloud Services<br>IT Managed Services, software and hardware</p>
    <p class="back-web">www.meridianit.com.au</p>
  </section>
</main>
</body>
</html>
```